Wildlfower Field Guide Needs a Book Cover Design

We need a book cover design in formats compatible with Adobe Illustrator and/or Photoshop (vector file that can be edited). I have attached a Power Point file with the general design features for the front and back covers and photographs to be used in the book cover. The cover size is 6" wide by 9" high (same size as the attached Power Point file). The book cover should have the same format including photos as the attached file with a similar color scheme. We are looking for a sky blue background then title text in a complementary darker blue. The other color elements (borders around photos) can be the same darker blue or dark gray. We are looking for better text types/styles for the title than those is the attached file. All three lines of the title should have the same width (1st line - thicker text, 2nd line - white italics on dark background, 3rd line - narrow text). The dark background on the 2nd line would ideally have some texture or style like a trail. On the back cover, written paragraphs should remain in Ebrima font.

Requirements
Must have
• Project should follow general cover outline of attached Power Point file
• Should have desired color scheme
• Must include all photos as formatted in the attached in the Power point file
Nice to have
• The title (2nd line) can be a solid color matching 1st line text or texture like a hiking trail

```html
<!DOCTYPE html>
<html lang="en">
<head>
<meta charset="utf-8">
<title>Desert Blooms Beside The Path – Cover Spread</title>
<link rel="stylesheet" href="https://fonts.googleapis.com/css2?family=Crimson+Pro:ital,wght@1,500&family=Noto+Sans:wght@400;700&family=PT+Sans+Narrow:wght@700&family=PT+Sans:wght@700&display=swap">
<style>
  :root {
    --navy: #1b3a70;
    --spine-text: #f1ebcf;
    --white: #ffffff;
    --sky-top: #8ea7cd;
    --sky-mid: #dde5f0;
    --dune-low: #a7bbd9;
    --dune-deep: #8aa2c8;
    --body-text: #1d2230;
  }
  * { margin: 0; padding: 0; box-sizing: border-box; }
  html, body { width: 1200px; height: 1200px; overflow: hidden; background: var(--white); }
  .canvas { position: relative; width: 1200px; height: 1200px; }

  .cover-panel { position: absolute; top: 142px; height: 779px; }
  .back-cover  { left: 42px; width: 520px;
    background: linear-gradient(180deg, var(--sky-top) 0%, #b9c9e0 22%, var(--sky-mid) 48%, #c5d3e7 56%, var(--dune-low) 78%, var(--dune-deep) 100%); }
  .front-cover { left: 639px; width: 520px;
    background:
      radial-gradient(ellipse 60% 30% at 55% 45%, rgba(255,255,255,.85), rgba(255,255,255,0) 70%),
      linear-gradient(180deg, #9bb1d3 0%, #d4deec 28%, #eef2f8 48%, #cbd7e9 58%, var(--dune-low) 80%, var(--dune-deep) 100%); }
  .spine { position: absolute; left: 562px; top: 142px; width: 77px; height: 779px; background: var(--navy); }
  .trim-band { position: absolute; left: 42px; top: 916px; width: 1117px; height: 5px; background: var(--navy); }

  .photo { position: absolute; border: 3px solid var(--navy); }
  .photo.yellow { background: radial-gradient(circle at 50% 50%, #f6e24a 0%, #ecd21c 45%, #6d6a3c 100%); }
  .photo.red    { background: radial-gradient(circle at 50% 50%, #ffcc33 0%, #f23b1c 35%, #b8141c 75%, #3a2a1a 100%); }
  .photo.cactus-yellow { background: radial-gradient(circle at 50% 55%, #ffd84a 0%, #f2d21a 50%, #b0a03a 100%); }

  .blurb {
    position: absolute; left: 231px; top: 433px; width: 266px;
    font-family: "Noto Sans", sans-serif; font-size: 13.6px; line-height: 20.2px;
    color: var(--body-text); text-align: justify;
  }
  .author-bio {
    position: absolute; left: 102px; top: 795px; width: 258px;
    font-family: "Noto Sans", sans-serif; font-size: 9.6px; line-height: 14.4px; color: var(--body-text);
  }
  .isbn-box { position: absolute; left: 374px; top: 794px; width: 127px; height: 74px; background: var(--white); }

  .type-layer { position: absolute; left: 0; top: 0; }
  .author      { font-family: "PT Sans", sans-serif; font-weight: 700; fill: var(--white); }
  .title-main  { font-family: "PT Sans Narrow", sans-serif; font-weight: 700; fill: var(--navy); }
  .title-trail { font-family: "Crimson Pro", serif; font-style: italic; font-weight: 500; fill: var(--navy); }
  .title-place { font-family: "Noto Sans", sans-serif; font-weight: 700; fill: var(--navy); }
  .title-place-light { font-family: "Noto Sans", sans-serif; font-weight: 400; fill: var(--navy); }
  .spine-author { font-family: "PT Sans", sans-serif; font-weight: 700; fill: var(--spine-text); }
  .spine-title  { font-family: "PT Sans Narrow", sans-serif; font-weight: 700; fill: var(--white); }
  .spine-small  { font-family: "Noto Sans", sans-serif; font-weight: 400; fill: var(--white); }
  .spine-bold   { font-family: "Noto Sans", sans-serif; font-weight: 700; fill: var(--white); }
</style>
</head>
<body>
<div class="canvas">
  <section class="cover-panel back-cover" role="img" aria-label="Pale blue sky over rippled white sand dunes"></section>
  <section class="cover-panel front-cover" role="img" aria-label="Pale blue sky over rippled white sand dunes"></section>
  <div class="spine"></div>
  <div class="trim-band"></div>

  <div class="photo cactus-yellow" style="left:102px;top:434px;width:109px;height:108px" role="img" aria-label="Yellow cactus flower close-up"></div>
  <div class="photo red" style="left:102px;top:554px;width:109px;height:107px" role="img" aria-label="Red cactus flower close-up"></div>
  <div class="photo red" style="left:102px;top:672px;width:109px;height:106px" role="img" aria-label="Crimson cactus flower close-up"></div>

  <p class="blurb">This field guide, Desert Blooms Beside the Path: Arizona Sonoran Desert, provides photos and descriptions of 160 wildflowers commonly found along hiking trails in the Arizona Sonoran Desert. This field guide was specifically designed for hikers and nature enthusiasts interested in the wildflowers of the Arizona Sonoran Desert. The wildflowers in this field guide are those most commonly found in the many desert parks and areas around both Phoenix and Tucson. This easy-to-use field guide is organized to facilitate wildflower identification by color, shape, and size and help answer the question: What is that desert wildflower?</p>

  <p class="author-bio">DANIEL HARLOW holds a degree in environmental biology and has spent many years hiking hundreds of miles in the Arizona Sonoran Desert, studying desert plants, and photographing wildflowers.</p>

  <div class="isbn-box"></div>

  <div class="photo yellow" style="left:674px;top:531px;width:100px;height:93px" role="img" aria-label="Yellow four-petal wildflower"></div>
  <div class="photo yellow" style="left:785px;top:531px;width:100px;height:93px" role="img" aria-label="Yellow four-petal wildflower"></div>
  <div class="photo yellow" style="left:894px;top:531px;width:100px;height:93px" role="img" aria-label="Yellow four-petal wildflower"></div>
  <div class="photo yellow" style="left:674px;top:634px;width:100px;height:92px" role="img" aria-label="Yellow five-petal wildflower"></div>
  <div class="photo yellow" style="left:785px;top:634px;width:100px;height:92px" role="img" aria-label="Yellow five-petal wildflower"></div>
  <div class="photo yellow" style="left:894px;top:634px;width:100px;height:92px" role="img" aria-label="Yellow five-petal wildflower"></div>
  <div class="photo yellow" style="left:674px;top:737px;width:100px;height:92px" role="img" aria-label="Yellow daisy-like wildflower"></div>
  <div class="photo yellow" style="left:785px;top:737px;width:100px;height:92px" role="img" aria-label="Yellow daisy-like wildflower"></div>
  <div class="photo yellow" style="left:894px;top:737px;width:100px;height:92px" role="img" aria-label="Yellow daisy-like wildflower"></div>

  <svg class="type-layer" width="1200" height="1200" viewBox="0 0 1200 1200">
    <text class="author" x="100" y="238" font-size="48" textLength="376" lengthAdjust="spacingAndGlyphs">DANIEL HARLOW</text>
    <text class="title-main" x="102" y="340" font-size="92" textLength="398" lengthAdjust="spacingAndGlyphs">DESERT BLOOMS</text>
    <text class="title-trail" x="164" y="378" font-size="40" textLength="252" lengthAdjust="spacingAndGlyphs">Beside The Path</text>
    <text class="title-place" x="102" y="420" font-size="35" textLength="394" lengthAdjust="spacingAndGlyphs">Arizona Sonoran Desert</text>

    <text class="spine-author" transform="translate(588,178) rotate(90)" font-size="39" textLength="282" lengthAdjust="spacingAndGlyphs">DANIEL HARLOW</text>
    <text class="spine-title" transform="translate(594,641) rotate(90)" font-size="34" textLength="147" lengthAdjust="spacingAndGlyphs">DESERT BLOOMS</text>
    <text class="spine-small" transform="translate(581,642) rotate(90)" font-size="12.5" textLength="145" lengthAdjust="spacingAndGlyphs">Arizona Sonoran Desert</text>
    <rect x="583" y="802" width="34" height="2.5" fill="#ffffff"/>
    <text class="spine-bold" transform="translate(602,814) rotate(90)" font-size="19" textLength="58" lengthAdjust="spacingAndGlyphs">Beside</text>
    <text class="spine-bold" transform="translate(582,814) rotate(90)" font-size="19" textLength="70" lengthAdjust="spacingAndGlyphs">The Path</text>

    <text class="author" x="676" y="236" font-size="76" textLength="314" lengthAdjust="spacingAndGlyphs">DANIEL</text>
    <text class="author" x="674" y="306" font-size="76" textLength="318" lengthAdjust="spacingAndGlyphs">HARLOW</text>
    <text class="title-main" x="674" y="440" font-size="64" textLength="296" lengthAdjust="spacingAndGlyphs">DESERT BLOOMS</text>
    <text class="title-place-light" x="674" y="466" font-size="22" textLength="296" lengthAdjust="spacingAndGlyphs">Arizona Sonoran Desert</text>
    <rect x="997" y="394" width="3" height="66" fill="var(--navy)"/>
    <text class="title-place" x="1014" y="422" font-size="35" textLength="104" lengthAdjust="spacingAndGlyphs">Beside</text>
    <text class="title-place" x="1014" y="458" font-size="35" textLength="126" lengthAdjust="spacingAndGlyphs">The Path</text>
  </svg>
</div>
</body>
</html>
```